K SPIRES Business Card Design

Need a business card design for K Spires, we're a tower company - our main scope of work is to upgrade cellular sites: swap antennas, install new coax, fiber, replace mounts, etc. Mostly tower work.

would like to see a sharp business card design with our logo either on background or with tower image on the background - something describing our field not only in words but in images.

Target Market(s)

USA

Industry/Entity Type

Business

Contact Information for Business Card

Tarnek Obliva
Operations Manager
K Spires LLC

cell 555-318-2094
tarnek@k-spires-example.com

4185 Wexbridge Commerce Pkwy, Suite D
Norcross, GA, 30571

Requirements
Must have
• some tower related design
Nice to have
• some tower or cellular antennas on the background, if possible to compliment our logo...

```html
<!DOCTYPE html>
<html lang="en">
<head>
<meta charset="utf-8">
<title>K Spires Business Card</title>
<link href="https://fonts.googleapis.com/css2?family=Lato:wght@400&family=Raleway:wght@400;500&display=swap" rel="stylesheet">
<style>
  :root {
    --stage-light: #efefef;
    --stage-dark: #c9c9c9;
    --card-glow: #575757;
    --card-mid: #2a2a2a;
    --card-edge: #050505;
    --text-light: #ffffff;
    --text-dark: #0a0a0a;
    --divider: rgba(255,255,255,0.12);
    --mark-faint: #0d0d0d;
  }
  * { margin: 0; padding: 0; box-sizing: border-box; }
  html, body { width: 1200px; height: 900px; overflow: hidden; }
  body {
    position: relative;
    background: radial-gradient(ellipse at 50% 45%, var(--stage-light) 0%, var(--stage-light) 35%, var(--stage-dark) 100%);
    font-family: "Lato", Arial, sans-serif;
  }
  .card {
    position: absolute;
    width: 543px;
    height: 319px;
    overflow: hidden;
    box-shadow: 0 2px 6px rgba(0,0,0,0.25);
  }
  .card-front {
    left: 351px; top: 98px;
    background: radial-gradient(ellipse 300px 230px at 48% 40%, var(--card-glow) 0%, var(--card-mid) 55%, var(--card-edge) 100%);
  }
  .card-back {
    left: 350px; top: 481px;
    width: 545px;
    background: radial-gradient(ellipse 330px 260px at 50% 25%, #4a4a4a 0%, var(--card-mid) 50%, var(--card-edge) 100%);
  }
  .divider {
    position: absolute;
    left: 266px; top: 86px;
    width: 1px; height: 212px;
    background: var(--divider);
  }
  .holder {
    position: absolute;
    right: 305px; top: 142px;
    text-align: right;
    white-space: nowrap;
  }
  .holder-name {
    font-family: "Raleway", Arial, sans-serif;
    font-weight: 400;
    font-size: 26px;
    color: var(--text-light);
    letter-spacing: 0.3px;
    line-height: 32px;
  }
  .holder-role {
    font-family: "Raleway", Arial, sans-serif;
    font-weight: 500;
    font-size: 16px;
    color: var(--text-dark);
    line-height: 18px;
  }
  .brand-name {
    position: absolute;
    left: 293px; top: 52px;
    font-family: "Lato", Arial, sans-serif;
    font-weight: 400;
    font-size: 44px;
    line-height: 1;
    color: var(--text-light);
  }
  .address {
    position: absolute;
    left: 293px; top: 146px;
    font-size: 15px;
    line-height: 17px;
    color: var(--text-light);
    white-space: nowrap;
  }
  .contact-list {
    position: absolute;
    left: 293px; top: 205px;
    list-style: none;
    color: var(--text-light);
    font-size: 15px;
    white-space: nowrap;
  }
  .contact-list li {
    display: flex;
    align-items: center;
    height: 21px;
  }
  .contact-list svg { width: 11px; height: 11px; margin-right: 6px; fill: #dddddd; flex: none; }
  .tower-art {
    position: absolute;
    left: 245px; top: 14px;
    width: 80px; height: 305px;
    background: linear-gradient(to bottom, rgba(70,70,70,0.25), rgba(40,40,40,0.45));
    clip-path: polygon(45% 0, 55% 0, 62% 25%, 80% 100%, 20% 100%, 38% 25%);
  }
  .brand-name-back {
    position: absolute;
    left: 0; right: 0; top: 170px;
    transform: translateY(-50%);
    text-align: center;
    font-family: "Lato", Arial, sans-serif;
    font-weight: 400;
    font-size: 68px;
    color: var(--mark-faint);
    line-height: 1;
  }
</style>
</head>
<body>

<section class="card card-front" aria-label="Business card front">
  <div class="holder">
    <p class="holder-name">TARNEK OBLIVA</p>
    <p class="holder-role">Operations Manager</p>
  </div>
  <div class="divider"></div>
  <p class="brand-name">K Spires</p>
  <p class="address">4185 Wexbridge Commerce Pkwy,<br>Suite D, Norcross, GA 30571</p>
  <ul class="contact-list">
    <li>
      <svg viewBox="0 0 12 12"><path d="M1 4c0-2 2-3 5-3s5 1 5 3l-2 1-1-1.5H4L3 5 1 4zm2 2h6l1.5 5h-9z"/></svg>
      555-318-2094
    </li>
    <li>
      <svg viewBox="0 0 12 12"><path d="M1 2.5h10v7H1zM1.6 3.2 6 6.6l4.4-3.4v.9L6 7.5 1.6 4.1z"/></svg>
      tarnek@k-spires-example.com
    </li>
    <li>
      <svg viewBox="0 0 12 12"><path d="M7.5 1.5a2.5 2.5 0 0 1 3 3L9 6 8 5l1.3-1.3a1 1 0 0 0-1-1L7 4 6 3zM4.5 10.5a2.5 2.5 0 0 1-3-3L3 6l1 1-1.3 1.3a1 1 0 0 0 1 1L5 8l1 1zM4 7.3 7.3 4l.7.7L4.7 8z"/></svg>
      www.k-spires-example.com
    </li>
  </ul>
</section>

<section class="card card-back" aria-label="Business card back">
  <div class="tower-art" role="img" aria-label="Faint cell tower with antennas in the background"></div>
  <p class="brand-name-back">K Spires</p>
</section>

</body>
</html>
```